Design a New Business Card for Our Company

We are looking for fresh, unique, and a modern business card that reflects our roots as digital marketing agency focused on SEM.

Industry/Entity Type

Marketing

Contact Information for Business Card

looking for very unique out of the box designs. clean and modern that compliments our logo

Requirements
Must have
• colors should match our logo
• Front should have name, address, email, and phone/fax of the person, phone/fax are the same number
• back should have our url

```html
<!DOCTYPE html>
<html lang="en">
<head>
<meta charset="utf-8">
<title>Northlane Solutions — Business Card</title>
<link rel="stylesheet" href="https://fonts.googleapis.com/css2?family=Arimo:wght@400;700&display=swap">
<style>
  :root {
    --backdrop: #3b3331;
    --card: #1c1c1d;
    --card-edge: #111112;
    --grey-light: #c9c9c9;
    --grey-mid: #9a9a9a;
    --blue: #5b9bd8;
    --white: #f1f1f1;
    --divider: #8a8a8a;
  }
  * { margin: 0; padding: 0; box-sizing: border-box; }
  html, body {
    width: 1200px; height: 787px; overflow: hidden;
    background: var(--backdrop);
    font-family: "Arimo", Arial, sans-serif;
  }
  .stage {
    position: relative; width: 1200px; height: 787px;
  }
  .card {
    position: absolute; top: 235px;
    width: 530px; height: 310px;
    background: var(--card);
    border: 1px solid var(--card-edge);
    box-shadow: 0 14px 30px rgba(0,0,0,0.45);
  }
  /* back side */
  .card--back { left: 45px; }
  .brand {
    position: absolute; left: 60px; top: 80px;
    display: flex; align-items: center; gap: 18px;
  }
  .brand__dot {
    width: 54px; height: 54px; border-radius: 50%;
    background: var(--grey-mid);
  }
  .brand__name {
    color: var(--grey-light); font-weight: 700;
    font-size: 50px; line-height: 1; letter-spacing: -1px;
  }
  .brand__tag {
    position: absolute; left: 132px; top: 142px;
    color: var(--grey-mid); font-size: 15px; letter-spacing: 14px;
  }
  .card__url {
    position: absolute; left: 60px; bottom: 48px;
    color: var(--white); font-size: 14px; letter-spacing: 7px;
  }
  /* front side */
  .card--front { left: 625px; }
  .front-mark {
    position: absolute; left: 40px; top: 0; bottom: 0; width: 170px;
    display: flex; flex-direction: column; align-items: center; justify-content: center; gap: 16px;
  }
  .front-mark__dot {
    width: 92px; height: 92px; border-radius: 50%; background: var(--blue);
  }
  .front-mark__name {
    color: var(--grey-light); font-weight: 700; font-size: 22px;
  }
  .divider {
    position: absolute; left: 238px; top: 55px; bottom: 45px;
    width: 1px; background: linear-gradient(var(--card), var(--divider), var(--card));
  }
  .contact {
    position: absolute; left: 262px; top: 72px; color: var(--white);
  }
  .contact__name { color: var(--grey-light); font-weight: 700; font-size: 20px; }
  .contact__title { color: var(--blue); font-size: 16px; margin-top: 3px; }
  .contact__address { font-size: 16px; line-height: 1.3; margin-top: 12px; }
  .contact__list { list-style: none; margin-top: 12px; font-size: 16px; }
  .contact__list li { display: flex; align-items: center; gap: 10px; line-height: 1.55; }
  .contact__list svg { width: 16px; height: 14px; fill: var(--grey-light); flex: none; }
</style>
</head>
<body>
<main class="stage">
  <section class="card card--back" aria-label="Card back">
    <div class="brand">
      <span class="brand__dot"></span>
      <span class="brand__name">northlane</span>
    </div>
    <div class="brand__tag">SOLUTIONS</div>
    <p class="card__url">www.northlane.com</p>
  </section>

  <section class="card card--front" aria-label="Card front">
    <div class="front-mark">
      <span class="front-mark__dot"></span>
      <span class="front-mark__name">northlane</span>
    </div>
    <span class="divider"></span>
    <div class="contact">
      <p class="contact__name">Mark Ellison</p>
      <p class="contact__title">President</p>
      <p class="contact__address">2147 Harbor View Lane<br>Cedar Grove, NY 11020</p>
      <ul class="contact__list">
        <li>
          <svg viewBox="0 0 16 14" aria-hidden="true"><path d="M1 4c0-2 3-3 7-3s7 1 7 3v1h-4V4H5v1H1z"/><path d="M3 7h10l1 6H2z"/></svg>
          412 5590 1834
        </li>
        <li>
          <svg viewBox="0 0 16 14" aria-hidden="true"><rect x="4" y="0" width="8" height="5"/><rect x="1" y="5" width="14" height="7" rx="1"/><rect x="4" y="10" width="8" height="4" fill="#1c1c1d"/></svg>
          712 3308 4419
        </li>
        <li>
          <svg viewBox="0 0 16 14" aria-hidden="true"><path d="M1 2h14v10H1z"/><path d="M1 2l7 6 7-6" fill="none" stroke="#1c1c1d" stroke-width="1.4"/></svg>
          mark@northlane.com
        </li>
      </ul>
    </div>
  </section>
</main>
</body>
</html>
```